Valdrin Insight Powerpoint

Take an outdated PowerPoint and modernize it to our company's brand via google PowerPoint. Please check out our website at www.valdrinpartners-example.com to see more styles but give it that intelligence twist. The powerpoint to work on is the Insight PP. Please keep it professional.

Target Market(s)

Security Industry / Silicon Valley

Industry/Entity Type

Executive Protection / Intelligence

Requirements
Must have
• Valdrin Logo / Valdrin Colors / Confidential notice at bottom
Nice to have
• Pictures of major cities / San Francisco
Should not have
• Pictures of anybody with ear pieces.

```html
<!DOCTYPE html>
<html lang="en">
<head>
<meta charset="utf-8">
<title>Valdrin Insight – DARE-Q</title>
<link rel="stylesheet" href="https://fonts.googleapis.com/css2?family=Orbitron:wght@700&family=Open+Sans:wght@400;600&family=Catamaran:wght@400;600&display=swap">
<style>
  :root {
    --band: #454547;
    --band-dark: #38383a;
    --brand-red: #8b171c;
    --white: #ffffff;
    --ink: #3a3a3a;
    --muted: #7a7a7c;
    --rule: #d9d9db;
    --photo-dark: #1c1c1e;
    --photo-mid: #5a5a5c;
  }
  * { box-sizing: border-box; margin: 0; padding: 0; }
  html, body { width: 1200px; height: 675px; overflow: hidden; background: var(--white); }
  .slide { position: relative; width: 1200px; height: 675px; background: var(--white); overflow: hidden; }
  .title-band {
    position: absolute; left: 0; top: 0; width: 1200px; height: 216px;
    background: linear-gradient(135deg, var(--band) 0%, var(--band-dark) 100%);
  }
  .title-accent {
    position: absolute; left: 0; top: 0; width: 1200px; height: 5px; background: var(--brand-red);
  }
  .slide-title {
    position: absolute; left: 82px; top: 40px; width: 1060px;
    font-family: "Orbitron", sans-serif; font-weight: 700;
    font-size: 25px; line-height: 36px; letter-spacing: 2px;
    color: var(--white); text-transform: uppercase; word-spacing: 8px;
  }
  .pillar { position: absolute; top: 131px; width: 339px; }
  .pillar-frame { background: var(--white); padding: 6px 7px 0; }
  .pillar-heading {
    height: 78px; background: var(--brand-red); color: var(--white);
    display: flex; align-items: center; justify-content: center; text-align: center;
    font-family: "Open Sans", sans-serif; font-weight: 400; font-size: 18.5px; line-height: 22px;
    text-transform: uppercase; padding: 0 6px;
  }
  .pillar-photo { height: 183px; }
  .photo-threat { background: radial-gradient(circle at 50% 40%, #4a4a4c 0%, var(--photo-dark) 75%); }
  .photo-network { background: radial-gradient(circle at 45% 40%, #8a8a8c 0%, #3c3c3e 55%, var(--photo-dark) 100%); }
  .photo-camera { background: linear-gradient(120deg, var(--photo-mid) 0%, #8e8e90 50%, #3e3e40 100%); }
  .pillar-text {
    margin-top: 13px; margin-left: -12px; margin-right: -12px; text-align: center;
    font-family: "Catamaran", sans-serif; font-weight: 400; font-size: 20px; line-height: 23px;
    color: var(--ink); white-space: nowrap;
  }
  .footer-rule {
    position: absolute; left: 82px; right: 82px; top: 612px; height: 1px; background: var(--rule);
  }
  .confidential-notice {
    position: absolute; left: 82px; top: 630px;
    font-family: "Open Sans", sans-serif; font-weight: 600; font-size: 10px; letter-spacing: 1.5px;
    color: var(--muted); text-transform: uppercase;
  }
  .confidential-notice strong { color: var(--brand-red); font-weight: 600; }
  .brand-mark {
    position: absolute; right: 82px; top: 625px;
    display: flex; align-items: center; gap: 7px;
    font-family: "Open Sans", sans-serif; font-weight: 600; font-size: 15px;
    color: var(--brand-red); text-transform: uppercase; letter-spacing: 1px;
  }
  .brand-mark .brand-square { width: 18px; height: 18px; background: var(--brand-red); }
</style>
</head>
<body>
<main class="slide">
  <div class="title-band"></div>
  <div class="title-accent"></div>
  <h1 class="slide-title">Digital Adversary Risk Evaluation-Quantification<br>(DARE-Q)</h1>

  <section class="pillar" style="left:82px">
    <div class="pillar-frame">
      <h2 class="pillar-heading">A methodology based on an<br>adversarial risk perspective</h2>
      <div class="pillar-photo photo-threat" role="img" aria-label="Hooded figure in darkness with digital interface overlays"></div>
    </div>
    <p class="pillar-text">Threat identification and<br>characterization identifies<br>adversaries most likely to exploit<br>risks in the client’s mission space or<br>personal life with empirical best fit<br>capabilities.</p>
  </section>

  <section class="pillar" style="left:448px">
    <div class="pillar-frame">
      <h2 class="pillar-heading">Likelihood and impact</h2>
      <div class="pillar-photo photo-network" role="img" aria-label="Laptop with a world map and connected network of people icons"></div>
    </div>
    <p class="pillar-text">Measures risk impact translated into<br>quantifiable variables consistent with<br>standards of evaluation from the<br>Intelligence Community and Cyber<br>Industry best practices.</p>
  </section>

  <section class="pillar" style="left:815px">
    <div class="pillar-frame">
      <h2 class="pillar-heading">Confidence reporting and<br>resiliency strategy</h2>
      <div class="pillar-photo photo-camera" role="img" aria-label="Security camera mounted on a concrete wall"></div>
    </div>
    <p class="pillar-text">Transparent reporting consistent with<br>Intelligence Community Analytic<br>Standards, supports RFI, and<br>continuous monitoring for indicator<br>updates as conditions change or new<br>information becomes available.</p>
  </section>

  <div class="footer-rule"></div>
  <p class="confidential-notice"><strong>Confidential</strong> · Valdrin Insight · Not for distribution</p>
  <div class="brand-mark"><span class="brand-square"></span><span>Valdrin Group</span></div>
</main>
</body>
</html>
```